business card for a massage therapy practice named 'Cedar and Willow Massage Studio'

I really need a trendy, yet easy on the eyes business card to complement my logo. Ideally with some gold or rose gold foil work.

My uploaded file of the logo I have in horizontal but I have a vertical version as well. Another color that is used in the website is a blush pink here and there. I'd like to see some trendy tropical leaves in the design.

```html
<!DOCTYPE html>
<html lang="en">
<head>
<meta charset="utf-8">
<title>Cedar and Willow Massage Studio – Business Card</title>
<link href="https://fonts.googleapis.com/css2?family=Work+Sans:wght@400;500&family=Dancing+Script:wght@600&display=swap" rel="stylesheet">
<style>
  :root {
    --backdrop: #bdb5ac;
    --card-dark: #2a2a2a;
    --card-light: #ffffff;
    --ink: #1e1e1e;
    --gold: #a8916a;
    --mint: #7fd3bd;
    --paper-text: #ffffff;
  }
  * { margin: 0; padding: 0; box-sizing: border-box; }
  html, body {
    width: 1200px;
    height: 930px;
    overflow: hidden;
    background: var(--backdrop);
    font-family: "Work Sans", Arial, sans-serif;
  }
  .canvas {
    position: relative;
    width: 1200px;
    height: 930px;
  }
  .card {
    position: absolute;
    width: 560px;
    height: 320px;
    border-radius: 18px;
    box-shadow: 0 6px 16px rgba(0,0,0,0.22);
  }

  /* Front of card */
  .card-front {
    left: 90px;
    top: 90px;
    background: linear-gradient(135deg, #333 0%, var(--card-dark) 55%, #222 100%);
    display: flex;
    align-items: center;
    justify-content: center;
  }
  .brand {
    display: flex;
    align-items: center;
    gap: 14px;
    font-family: "Work Sans", Arial, sans-serif;
    font-weight: 500;
    font-size: 26px;
    letter-spacing: 0.5px;
  }
  .brand-dot {
    width: 16px;
    height: 16px;
    border-radius: 50%;
    background: var(--gold);
    flex: none;
  }
  .card-front .brand-name { color: var(--paper-text); }

  /* Back of card */
  .card-back {
    left: 550px;
    top: 520px;
    background: var(--card-light);
  }
  .card-back .brand {
    position: absolute;
    left: 34px;
    top: 60px;
    font-size: 18px;
    gap: 10px;
  }
  .card-back .brand-dot { width: 12px; height: 12px; }
  .card-back .brand-name { color: var(--ink); }

  .holder-name {
    position: absolute;
    right: 40px;
    top: 120px;
    font-family: "Dancing Script", "Brush Script MT", cursive;
    font-weight: 600;
    font-size: 40px;
    color: var(--gold);
  }
  .divider {
    position: absolute;
    left: 34px;
    right: 34px;
    top: 178px;
    height: 2px;
    background: var(--gold);
  }
  .address {
    position: absolute;
    right: 40px;
    top: 192px;
    text-align: right;
    font-size: 14px;
    line-height: 1.4;
    color: var(--ink);
  }
  .contacts {
    position: absolute;
    left: 34px;
    top: 200px;
    list-style: none;
    font-size: 15px;
    line-height: 1.55;
    color: var(--ink);
  }
  .contacts li {
    display: flex;
    align-items: center;
    gap: 10px;
  }
  .contacts svg {
    width: 11px;
    height: 11px;
    flex: none;
  }
  .contacts .web-domain { color: var(--gold); }
</style>
</head>
<body>
<div class="canvas">

  <section class="card card-front" aria-label="Card front">
    <div class="brand">
      <span class="brand-dot"></span>
      <span class="brand-name">Cedar and Willow Massage Studio</span>
    </div>
  </section>

  <section class="card card-back" aria-label="Card back">
    <div class="brand">
      <span class="brand-dot"></span>
      <span class="brand-name">Cedar and Willow Massage Studio</span>
    </div>

    <p class="holder-name">Marisol Vega</p>
    <div class="divider"></div>

    <p class="address">482 Linden Ave. suite 210,<br>Fairhaven, CA 90210</p>

    <ul class="contacts">
      <li>
        <svg viewBox="0 0 12 12" aria-hidden="true"><path d="M2 1h3l1 3-2 1a7 7 0 0 0 3 3l1-2 3 1v3a1 1 0 0 1-1 1A10 10 0 0 1 1 2a1 1 0 0 1 1-1z" fill="var(--gold)"/></svg>
        (555) 214-0387
      </li>
      <li>
        <svg viewBox="0 0 12 12" aria-hidden="true"><rect x="1" y="2.5" width="10" height="7" fill="none" stroke="var(--gold)" stroke-width="1.2"/><path d="M1 3l5 4 5-4" fill="none" stroke="var(--gold)" stroke-width="1.2"/></svg>
        cedarandwillowstudio@gmail.com
      </li>
      <li>
        <svg viewBox="0 0 12 12" aria-hidden="true"><circle cx="6" cy="6" r="4.8" fill="none" stroke="var(--gold)" stroke-width="1.1"/><path d="M1.2 6h9.6M6 1.2c-2.4 3-2.4 6.6 0 9.6M6 1.2c2.4 3 2.4 6.6 0 9.6" fill="none" stroke="var(--gold)" stroke-width="1"/></svg>
        <span>www.<span class="web-domain">cedarandwillow</span>.com</span>
      </li>
    </ul>
  </section>

</div>
</body>
</html>
```